Business Card Design for Software Development Company

I am looking for a business card design the incorporates my new logo (attached below).

Key information to include:
Name: Martin Quelbrook
Title: CEO
Email: martin@brightwellcivic.example
Phone: 555-218-9403
Website: www.brightwellcivic.example

NOTE: This design should be easy to edit so that we can order cards for different members of our team.

```html
<!DOCTYPE html>
<html lang="en">
<head>
<meta charset="utf-8">
<title>Brightwell Civic Business Card</title>
<link href="https://fonts.googleapis.com/css2?family=Montserrat:wght@400;600;700&display=swap" rel="stylesheet">
<style>
  :root {
    --bg: #2a2d31;
    --card-white: #ffffff;
    --orange: #ee7a22;
    --orange-light: #f18d2f;
    --orange-deep: #e86d1e;
    --teal: #14b9a6;
    --red: #d9432f;
    --ink: #1d1d1f;
    --grey: #4a4a4a;
    --font: "Montserrat", "Helvetica Neue", Arial, sans-serif;
  }
  * { box-sizing: border-box; margin: 0; padding: 0; }
  html, body { width: 1200px; height: 900px; overflow: hidden; }
  body {
    background: var(--bg);
    font-family: var(--font);
    display: flex;
    flex-direction: column;
    align-items: center;
    justify-content: center;
    gap: 60px;
  }
  .card {
    width: 560px;
    height: 320px;
    border-radius: 26px;
    position: relative;
    overflow: hidden;
  }
  .brand {
    display: flex;
    align-items: center;
    gap: 12px;
  }
  .brand-dot {
    width: 16px;
    height: 16px;
    border-radius: 50%;
    flex: none;
  }
  .brand-name {
    font-weight: 600;
    font-size: 26px;
    letter-spacing: 3px;
    text-transform: uppercase;
    line-height: 1;
  }
  /* Front */
  .card-front { background: var(--card-white); padding: 42px 48px; }
  .card-front .brand-dot { background: var(--orange); }
  .card-front .brand-name { color: var(--ink); }
  .person { margin-top: 26px; }
  .person-name {
    font-weight: 700;
    font-size: 19px;
    letter-spacing: 0.5px;
    text-transform: uppercase;
  }
  .first-name { color: var(--teal); }
  .last-name { color: var(--orange); }
  .person-title {
    font-weight: 400;
    font-size: 14px;
    color: var(--grey);
    margin-top: 4px;
  }
  .contact-icons { display: flex; gap: 6px; margin-top: 8px; }
  .contact-icons svg { width: 16px; height: 16px; }
  .contact-list { list-style: none; margin-top: 10px; }
  .contact-list li {
    font-weight: 400;
    font-size: 13.5px;
    color: var(--grey);
    line-height: 1.55;
  }
  /* Back */
  .card-back {
    background: linear-gradient(135deg, var(--orange-light) 0%, var(--orange) 50%, var(--orange-deep) 100%);
    display: flex;
    align-items: center;
    justify-content: center;
  }
  .card-back .brand-dot { background: var(--card-white); width: 20px; height: 20px; }
  .card-back .brand-name { color: var(--card-white); font-size: 34px; letter-spacing: 4px; }
</style>
</head>
<body>

  <section class="card card-front" aria-label="Business card front">
    <div class="brand">
      <span class="brand-dot"></span>
      <span class="brand-name">Brightwell Civic</span>
    </div>

    <div class="person">
      <div class="person-name"><span class="first-name">Martin</span> <span class="last-name">Quelbrook</span></div>
      <div class="person-title">CEO</div>
    </div>

    <div class="contact-icons">
      <svg viewBox="0 0 16 16" aria-label="Phone">
        <circle cx="8" cy="8" r="7" fill="none" stroke="var(--red)" stroke-width="1.4"/>
        <rect x="5.8" y="4.2" width="4.4" height="7.6" rx="0.8" fill="var(--red)"/>
      </svg>
      <svg viewBox="0 0 16 16" aria-label="Email">
        <circle cx="8" cy="8" r="7" fill="none" stroke="var(--teal)" stroke-width="1.4"/>
        <rect x="4.3" y="5.5" width="7.4" height="5" rx="0.6" fill="var(--teal)"/>
        <path d="M4.5 5.8 L8 8.4 L11.5 5.8" fill="none" stroke="#fff" stroke-width="0.8"/>
      </svg>
      <svg viewBox="0 0 16 16" aria-label="Website">
        <circle cx="8" cy="8" r="7" fill="none" stroke="var(--orange)" stroke-width="1.4"/>
        <circle cx="8" cy="8" r="3.6" fill="none" stroke="var(--orange)" stroke-width="1"/>
        <path d="M4.4 8 H11.6 M8 4.4 V11.6" stroke="var(--orange)" stroke-width="0.8"/>
      </svg>
    </div>

    <ul class="contact-list">
      <li class="contact-phone">555-218-9403</li>
      <li class="contact-email">martin@brightwellcivic.example</li>
      <li class="contact-web">www.brightwellcivic.example</li>
    </ul>
  </section>

  <section class="card card-back" aria-label="Business card back">
    <div class="brand">
      <span class="brand-dot"></span>
      <span class="brand-name">Brightwell Civic</span>
    </div>
  </section>

</body>
</html>
```